Brightfen Business Card Redesign & Logo Update

We need to update our business cards to something more modern and fresh. Brightfen can provide the current color schemes and old design examples, but welcome creativity in helping us with this redesign. PLEASE NOTE that we no longer utilize the "tree" and/or "leaf" imagery in our branding. If able would apprecaite an update on the quality of our "words only" logo in Ai. / PNG formats too.

Target Market(s)

Investors, landowners, corporate partners, contractors

Industry/Entity Type

Environmental Restoration & Conservation

Contact Information for Business Card

Logo, persons name, title, mailing address, phone and email, website url

Font styles to use
Other font styles liked:
• Merriweather

Requirements
Nice to have
• Logo, persons name, title, mailing address, phone and email, website url, but open to ideams
Should not have
• No all back backgrounds

```html
<!DOCTYPE html>
<html lang="en">
<head>
<meta charset="utf-8">
<title>Brightfen Business Card</title>
<link rel="stylesheet" href="https://fonts.googleapis.com/css2?family=Merriweather:wght@400;700;900&display=swap">
<style>
  :root {
    --backdrop: #a7a7a7;
    --card: #ffffff;
    --green: #1a7a3a;
    --orange: #ee7f22;
    --ink: #1c1c1c;
  }
  html, body {
    margin: 0;
    padding: 0;
    width: 1146px;
    height: 1200px;
    overflow: hidden;
    background: var(--backdrop);
    font-family: "Merriweather", Georgia, serif;
  }
  .card {
    position: absolute;
    left: 176px;
    width: 797px;
    background: var(--card);
    overflow: hidden;
  }
  .card--front { top: 113px; height: 455px; }
  .card--back  { top: 595px; height: 468px; }

  .brand {
    font-family: "Merriweather", Georgia, serif;
    font-weight: 900;
    color: var(--green);
    letter-spacing: 1px;
    margin: 0;
    line-height: 1;
  }
  .front-logo {
    position: absolute;
    left: 0; right: 0; top: 0; bottom: 0;
    display: flex;
    align-items: center;
    justify-content: center;
    gap: 22px;
  }
  .front-logo .brand { font-size: 66px; }
  .brand-dot {
    width: 40px; height: 40px;
    border-radius: 50%;
    background: var(--orange);
  }

  .back-logo {
    position: absolute;
    left: 32px;
    top: 196px;
    width: 330px;
  }
  .back-logo .brand { font-size: 43px; }

  .divider {
    position: absolute;
    left: 390px;
    top: 93px;
    width: 2px;
    height: 238px;
    background: var(--orange);
  }
  .contact {
    position: absolute;
    left: 420px;
    top: 90px;
    color: var(--ink);
    font-size: 21px;
    line-height: 1.4;
  }
  .contact p { margin: 0; }
  .person-name {
    font-weight: 700;
    font-size: 26px;
    letter-spacing: 0.5px;
    line-height: 1.2;
  }
  .person-name .first { color: var(--orange); }
  .person-name .last  { color: var(--green); }
  .person-title { margin-bottom: 22px !important; }
  .address { margin-bottom: 18px !important; }
  .contact-line {
    display: flex;
    align-items: center;
    gap: 8px;
    line-height: 1.35;
  }
  .contact-line svg { width: 15px; height: 15px; flex: none; }

  .wave {
    position: absolute;
    left: 0; bottom: 0;
    width: 797px; height: 468px;
  }
</style>
</head>
<body>
  <section class="card card--front">
    <div class="front-logo">
      <span class="brand-dot"></span>
      <h1 class="brand">BRIGHTFEN</h1>
    </div>
  </section>

  <section class="card card--back">
    <svg class="wave" viewBox="0 0 797 468" aria-hidden="true">
      <path d="M0 420 C 260 420, 560 392, 797 318 L797 468 L0 468 Z" fill="var(--green)"/>
      <path d="M300 438 C 520 428, 690 385, 797 352 L797 322 C 690 360, 520 412, 300 438 Z" fill="var(--orange)"/>
      <path d="M0 420 C 260 420, 560 392, 797 318 L797 330 C 560 404, 260 430, 0 430 Z" fill="#ffffff"/>
    </svg>

    <div class="back-logo">
      <h2 class="brand">BRIGHTFEN</h2>
    </div>

    <div class="divider"></div>

    <div class="contact">
      <p class="person-name"><span class="first">MARCUS</span> <span class="last">HALE</span></p>
      <p class="person-title">Founder</p>
      <p>Your Company Address</p>
      <p class="address">Fenway Rd 48, PO 2210, OR</p>
      <p class="contact-line">
        <svg viewBox="0 0 16 16" aria-hidden="true"><path d="M3 2h3l1.5 3.5-2 1.3a8 8 0 0 0 3.7 3.7l1.3-2L14 10v3a1 1 0 0 1-1 1A11 11 0 0 1 2 3a1 1 0 0 1 1-1z" fill="var(--orange)"/></svg>
        (541) 555-0182
      </p>
      <p class="contact-line">
        <svg viewBox="0 0 16 16" aria-hidden="true"><rect x="1" y="3" width="14" height="10" fill="var(--orange)"/><path d="M1 3l7 5.5L15 3" fill="none" stroke="#fff" stroke-width="1.4"/></svg>
        marcus@brightfen.example
      </p>
      <p class="contact-line">
        <svg viewBox="0 0 16 16" aria-hidden="true"><circle cx="8" cy="8" r="7" fill="var(--orange)"/><path d="M1 8h14M8 1c-3 3.5-3 10.5 0 14M8 1c3 3.5 3 10.5 0 14" fill="none" stroke="#fff" stroke-width="1"/></svg>
        www.brightfen.example
      </p>
    </div>
  </section>
</body>
</html>
```